Larkspur Talent IT Recruiting firm needs a business card design for Recruiters, Sourcers, and Account

We need business cards that allow us to change all contact info, names, titles (Recruiter, Sourcer, Account Manager, Director, CEO, etc) per person since we have three offices, in three cities, Phoenix, Austin, and Las Vegas. We do recruiting and contractors for IT positions (Developers, Architects, Software Engineers, Security Engineers, Help Desk, DBAs, PMs, Scrum Masters, etc.) Our client companies are very diverse from Meridian 100 to silicone Valley type start-ups.

So, while we what hip, techie, and quirky, it still needs to be professional. Primary color we use is blue, with silver as a secondary color.

Target Market(s)

IT, Technology

Industry/Entity Type

Business

Contact Information for Business Card

Company name: Larkspur Talent, Inc.
Website: www.larkspurtalent.example
Logos for Careerloop, Blipster, and Myriada

Name, Title, Office Number, Cell Number, email

Font styles to use
Serif
Sans Serif

Colors
0455a3
d5d5d5

Requirements
Nice to have
• The grey I selected below is not necessary - but, would like silver included. I included a card design (File 3: LTI early trial example.jpg) that I had started on. It's very rough, and not quite what we're looking for, but what we did like is the logo, big, maybe a bit faded, off center, goes out of frame, etc. Still looking for other ideas - you are the pros! But, just an idea of a design element we liked.

```html
<!DOCTYPE html>
<html lang="en">
<head>
<meta charset="utf-8">
<title>Larkspur Talent — Business Card</title>
<link href="https://fonts.googleapis.com/css2?family=Cinzel:wght@400&family=Source+Sans+3:wght@400;700&display=swap" rel="stylesheet">
<style>
  :root {
    --brand-blue: #0455a3;
    --silver: #d5d5d5;
    --silver-dark: #a8a8a8;
    --ink: #1c1c1c;
    --text-grey: #3a3a3a;
    --card-white: #ffffff;
    --backdrop: #e8e5e0;
  }
  * { box-sizing: border-box; margin: 0; padding: 0; }
  html, body {
    width: 1200px;
    height: 1093px;
    overflow: hidden;
    background: var(--backdrop);
  }
  .card {
    position: absolute;
    width: 842px;
    height: 480px;
    background: var(--card-white);
    border-radius: 40px;
    overflow: hidden;
    box-shadow: 0 2px 6px rgba(0,0,0,.25);
  }
  .card--back { left: 306px; top: 44px; }
  .card--front { left: 47px; top: 556px; }

  .company-name {
    position: absolute;
    font-family: "Cinzel", serif;
    font-weight: 400;
    color: var(--ink);
    line-height: 1;
    white-space: nowrap;
  }
  .card--back .company-name {
    left: 30px; width: 440px; top: 168px;
    text-align: center;
    font-size: 37px; letter-spacing: 2px;
  }
  .card--front .company-name {
    left: 0; right: 0; top: 140px;
    text-align: center;
    font-size: 56px; letter-spacing: 4px;
  }

  .tagline {
    position: absolute;
    font-family: "Cinzel", serif;
    font-weight: 400;
    color: var(--text-grey);
    letter-spacing: 3px;
    white-space: nowrap;
    text-align: center;
  }
  .card--back .tagline { left: 30px; width: 440px; top: 234px; font-size: 18px; }
  .card--front .tagline { left: 0; right: 0; top: 262px; font-size: 23px; }

  .divider {
    position: absolute;
    left: 490px; top: 99px;
    width: 2px; height: 246px;
    background: var(--silver);
  }

  .contact {
    position: absolute;
    left: 522px; top: 100px;
    font-family: "Source Sans 3", sans-serif;
    color: var(--text-grey);
  }
  .contact__name { font-size: 29px; font-weight: 700; color: var(--brand-blue); line-height: 1.1; }
  .contact__title { font-size: 19px; margin-top: 6px; }
  .contact__list { list-style: none; margin-top: 16px; }
  .contact__item {
    display: flex; align-items: center; gap: 8px;
    font-size: 19px; height: 32px;
  }
  .contact__icon { width: 16px; height: 16px; flex: none; }

  .accent-bands {
    position: absolute; left: 0; bottom: 0;
    width: 100%;
  }
  .accent-bands__silver {
    height: 22px;
    background: linear-gradient(90deg, var(--silver-dark), #f2f2f2 40%, var(--silver) 70%, var(--silver-dark));
  }
  .accent-bands__gap { height: 6px; background: var(--card-white); }
  .accent-bands__blue { height: 40px; background: var(--brand-blue); }

  .website {
    position: absolute; left: 0; right: 0; top: 366px;
    text-align: center;
    font-family: "Source Sans 3", sans-serif;
    font-size: 26px; letter-spacing: 3px;
    color: var(--ink);
  }
</style>
</head>
<body>

<section class="card card--back" aria-label="Card back with contact details">
  <p class="company-name">LARKSPUR TALENT</p>
  <p class="tagline">BUILDING TEAMS THAT LAST</p>

  <div class="divider"></div>

  <div class="contact">
    <h1 class="contact__name">Maren Ellison</h1>
    <p class="contact__title">First Touch Embassador</p>
    <ul class="contact__list">
      <li class="contact__item">
        <svg class="contact__icon" viewBox="0 0 20 20"><path d="M5 2l3 4-2 2c1 2.5 3 4.5 5.5 5.5l2-2 4 3-2 3.5C9 17.5 2.5 11 1.5 4.5z" fill="none" stroke="var(--brand-blue)" stroke-width="1.8"/></svg>
        555-010-2734
      </li>
      <li class="contact__item">
        <svg class="contact__icon" viewBox="0 0 20 20"><rect x="1" y="4" width="18" height="13" rx="2" fill="var(--brand-blue)"/><path d="M2 6l8 6 8-6" fill="none" stroke="#fff" stroke-width="1.6"/></svg>
        maren@larkspurtalent.example
      </li>
      <li class="contact__item">
        <svg class="contact__icon" viewBox="0 0 20 20"><g fill="none" stroke="var(--brand-blue)" stroke-width="1.6"><circle cx="10" cy="10" r="8.5"/><ellipse cx="10" cy="10" rx="4" ry="8.5"/><path d="M1.5 10h17M3 5.5h14M3 14.5h14"/></g></svg>
        www.larkspurtalent.example
      </li>
      <li class="contact__item">
        <svg class="contact__icon" viewBox="0 0 20 20"><circle cx="10" cy="10" r="9" fill="var(--brand-blue)"/></svg>
        @MarenEllisonLT
      </li>
      <li class="contact__item">
        <svg class="contact__icon" viewBox="0 0 20 20"><rect x="1.5" y="1.5" width="17" height="17" rx="3" fill="var(--brand-blue)"/></svg>
        @MarenEllisonLT
      </li>
    </ul>
  </div>

  <div class="accent-bands" aria-hidden="true">
    <div class="accent-bands__silver"></div>
    <div class="accent-bands__gap"></div>
    <div class="accent-bands__blue"></div>
  </div>
</section>

<section class="card card--front" aria-label="Card front">
  <p class="company-name">LARKSPUR TALENT</p>
  <p class="tagline">BUILDING TEAMS THAT LAST</p>
  <p class="website">www.larkspurtalent.example</p>
</section>

</body>
</html>
```